Marwick Partners Exit Plan business consultant web site

This website is for a consulting business that helps other businesses with exit plans. Essentially, assists them with the sale of their business. This website should be very professional, almost with a wall street look. I would like a very attractive image on the homepage. Perhaps something that denotes success. Perhaps a picture of palm trees and a beach? I will leave it to you for interpretation.

Across the screen I would like the words "Does your business have an exit plan?"

Below that it should read the following:
Let us help you with a completely impartial, no obligation assessment (button with link to the contact page)

Also, please use logo in a prominent place on the website so it's easily seen.

Target Market(s)

Males 40+

Coding

Coded - Design and coding required

Number of Pages Required

5+ page

Colors

Designer to choose colors to be used in the design.

Requirements
Must have
• The tabs for the homepage on the top should be:
• 1. About us
• 2. Services
• 3. Industries
• 4. Our success
• 5. Contact
Nice to have
• Clean, professional image.
• Please put FB, Twitter, Linked In - logos at bottom.
• Here are two examples of a website to give you an idea:
• https://notes.quelvarocapital.example/library/why-every-business-owner-should-have-an-exit-plan
Should not have
• nothing whimsical or cartoon like

```html
<!DOCTYPE html>
<html lang="en">
<head>
<meta charset="utf-8">
<title>Marwick Partners — Exit Planning</title>
<link rel="stylesheet" href="https://fonts.googleapis.com/css2?family=Exo+2:wght@300;400;500&family=Arimo:wght@400&display=swap">
<style>
:root{
  --ink:#1b1b1b;
  --text:#333333;
  --muted:#555555;
  --accent:#1a8fd6;
  --grey-band:#eeeeee;
  --footer:#000000;
  --white:#ffffff;
  --rule:#2a2a2a;
}
*{box-sizing:border-box;margin:0;padding:0}
html,body{width:1200px;height:2696px;overflow:hidden}
body{position:relative;background:var(--white);color:var(--text);font-family:"Arimo",Arial,sans-serif}
.abs{position:absolute}

/* header */
.site-header{left:0;top:0;width:1200px;height:113px;background:var(--white)}
.brand{left:172px;top:22px;display:flex;align-items:center;gap:10px}
.brand-mark{width:22px;height:22px;background:var(--ink)}
.brand-name{font-family:"Exo 2",sans-serif;font-weight:400;font-size:24px;color:var(--ink);letter-spacing:.5px}
.phone{right:175px;top:26px;display:flex;align-items:center;gap:8px;font-family:"Exo 2",sans-serif;font-weight:300;font-size:21px;color:var(--ink)}
.main-nav{right:175px;top:76px;display:flex;gap:38px;font-family:"Exo 2",sans-serif;font-weight:300;font-size:17px;color:var(--ink)}
.main-nav span{padding-bottom:6px}
.main-nav .current{border-bottom:2px solid var(--ink)}

/* hero */
.hero{left:0;top:113px;width:1200px;height:492px;background:linear-gradient(180deg,#1e2329 0%,#2a3038 55%,#0b0c0e 72%,#1b1f24 100%)}
.hero-title{left:172px;top:238px;font-family:"Exo 2",sans-serif;font-weight:400;font-size:47px;line-height:53px;color:var(--white)}
.hero-sub{left:172px;top:361px;font-family:"Exo 2",sans-serif;font-weight:400;font-size:18px;line-height:22px;color:var(--white)}
.hero-btn{left:172px;top:428px;width:141px;height:43px;background:var(--accent);color:var(--white);font-family:"Exo 2",sans-serif;font-weight:500;font-size:15px;display:flex;align-items:center;justify-content:center}
.slider-dots{left:484px;top:560px;display:flex;gap:9px}
.slider-dots span{width:52px;height:6px;background:var(--white)}
.slider-dots .outline{background:transparent;border:2px solid var(--white)}

/* welcome */
.welcome-title{left:172px;top:674px;font-family:"Exo 2",sans-serif;font-weight:300;font-size:50px;line-height:50px;color:var(--ink)}
.lead{left:172px;top:796px;width:444px;font-family:"Exo 2",sans-serif;font-weight:300;font-size:18.5px;line-height:26px;color:var(--ink);text-align:justify}
.body-copy{left:172px;width:444px;font-size:12.6px;line-height:21.8px;color:var(--muted);text-align:justify}
.sub-head{left:172px;font-family:"Exo 2",sans-serif;font-weight:500;font-size:18px;color:var(--ink)}
.points{left:172px;top:1355px;list-style:none;font-size:12.6px;line-height:24.8px;color:var(--text)}
.points li::before{content:"";display:inline-block;width:6px;height:6px;border-radius:50%;background:#bbbbbb;margin-right:10px;vertical-align:middle}
.welcome-photo{left:696px;top:663px;width:329px;height:397px;background:#111;padding:13px}
.welcome-photo .fill{width:100%;height:100%;background:linear-gradient(135deg,#7b8088 0%,#3b3f45 60%,#1d1f22 100%);border:4px solid var(--white)}

/* services */
.services{left:0;top:1543px;width:1200px;height:472px;background:var(--grey-band)}
.section-title{font-family:"Exo 2",sans-serif;font-weight:300;font-size:52px;color:var(--ink)}
.service{width:244px;height:88px;display:flex}
.service-icon{width:80px;height:88px;border:2px solid var(--rule);background:var(--white);box-shadow:3px 3px 0 #bdbdbd;flex:none;display:flex;align-items:center;justify-content:center}
.service-icon .fill{width:48px;height:48px;background:linear-gradient(135deg,#d8d8d8,#9a9a9a);border-radius:4px}
.service-body{border-top:2px solid var(--rule);padding:12px 0 0 12px;flex:1}
.service-body h3{font-family:"Exo 2",sans-serif;font-weight:400;font-size:21px;color:var(--ink);margin-bottom:10px;padding-left:3px}
.service-body p{font-size:12.6px;line-height:19.5px;color:var(--muted)}

/* news */
.news-photo{width:205px;height:180px}
.news-title{width:200px;font-family:"Exo 2",sans-serif;font-weight:400;font-size:19px;line-height:23.5px;color:var(--ink)}
.news-text{width:195px;font-size:11px;line-height:18.7px;color:var(--muted)}
.news-date{display:flex;align-items:center;gap:5px;font-family:"Exo 2",sans-serif;font-size:13px;color:#8a8a8a}

/* footer */
.site-footer{left:0;top:2441px;width:1200px;height:255px;background:var(--footer);border-top:3px solid #555}
.social{left:502px;top:2508px;display:flex;gap:12px}
.social span{width:46px;height:51px;border:2px solid var(--white)}
.footer-nav{left:0;top:2589px;width:1200px;display:flex;justify-content:center;gap:32px;font-family:"Exo 2",sans-serif;font-weight:300;font-size:16px;color:var(--white)}
.copyright{left:0;top:2631px;width:1200px;text-align:center;font-family:"Exo 2",sans-serif;font-weight:300;font-size:14px;color:var(--white)}
</style>
</head>
<body>

<header class="abs site-header">
  <div class="abs brand"><span class="brand-mark"></span><span class="brand-name">Marwick Partners</span></div>
  <div class="abs phone">
    <svg width="22" height="22" viewBox="0 0 24 24" fill="none" stroke="#1b1b1b" stroke-width="1.4"><path d="M5 3h4l2 5-2.5 1.5a11 11 0 0 0 6 6L16 13l5 2v4a2 2 0 0 1-2 2A17 17 0 0 1 3 5a2 2 0 0 1 2-2z"/></svg>
    Call Us: 125 555 0148
  </div>
  <nav class="abs main-nav">
    <span class="current">Home</span><span>About Us</span><span>Services</span><span>Industries</span><span>Our Success</span><span>Contact</span>
  </nav>
</header>

<section class="abs hero" role="img" aria-label="Silhouettes of business people in a high-rise office overlooking a city at dusk"></section>
<h1 class="abs hero-title">Does your business<br>have an exit plan?</h1>
<p class="abs hero-sub">Let us help you with a completely impartial,<br>no obligation assessment</p>
<a class="abs hero-btn">CONTACT US</a>
<div class="abs slider-dots"><span></span><span class="outline"></span><span></span><span></span></div>

<h2 class="abs welcome-title">Welcome to<br>Marwick Partners</h2>
<p class="abs lead">Sed ut perspiciatis unde omnis iste natus error sit voluptatem accusantium doloremquedant ium, totam rem aperiam</p>
<p class="abs body-copy" style="top:888px">Sed ut perspiciatis unde omnis iste natus error sit voluptatem accusantium doloremque laudantium, totam rem aperiam, eaque ipsa quae ab illo inventore veritatis et quasi architecto beatae vitae dicta sunt explicabo. Nemo enim ipsam voluptatem quia voluptas sit aspernatur aut odit aut fugit, sed quia consequuntur magni dolores eos qui ratione voluptatem sequi nesciunt. Neque porro quisquam est, qui dolorem ipsum quia dolor sit amet, consectetur, adipisci velit, sed quia non numquam eius modi.</p>
<h3 class="abs sub-head" style="top:1080px;left:174px">A Difficult Topic for Many Business Owners</h3>
<p class="abs body-copy" style="top:1120px">Sed ut perspiciatis unde omnis iste natus error sit voluptatem accusantium doloremque laudantium, totam rem aperiam, eaque ipsa quae ab illo inventore veritatis et quasi architecto beatae vitae dicta sunt explicabo. Nemo enim ipsam voluptatem quia voluptas sit aspernatur.</p>
<h3 class="abs sub-head" style="top:1232px">Assembling an Exit-Planning Team</h3>
<p class="abs body-copy" style="top:1272px">Sed ut perspiciatis unde omnis iste natus error sit voluptatem accusantium doloremque laudantium, totam rem aperiam, eaque ipsa quae ab illo inventore veritatis et quasi architecto beatae vitae dicta sunt explicabo.</p>
<ul class="abs points">
  <li>Praesent vestibulum diam et lacinia hendrerit.</li>
  <li>Duis vel metus quis tellus placerat posuere at dapibus sem.</li>
  <li>Fusce vitae arcu tempus, porttitor libero ac, imperdiet velit.</li>
  <li>Morbi rhoncus est pulvinar condimentum rutrum.</li>
  <li>Etiam in leo at nisi posuere dapibus.</li>
</ul>
<div class="abs welcome-photo"><div class="fill" role="img" aria-label="Business people shaking hands in a bright office"></div></div>

<section class="abs services"></section>
<h2 class="abs section-title" style="left:172px;top:1603px">Our Services</h2>

<div class="abs service" style="left:172px;top:1720px"><div class="service-icon"><div class="fill" role="img" aria-label="Team meeting icon"></div></div><div class="service-body"><h3>Service Name</h3><p>Sed ut perspiciatis undeite natus error sittsantium</p></div></div>
<div class="abs service" style="left:477px;top:1720px"><div class="service-icon"><div class="fill" role="img" aria-label="Financial growth icon"></div></div><div class="service-body"><h3>Service Name</h3><p>Sed ut perspiciatis undeise natus error sittsantium</p></div></div>
<div class="abs service" style="left:781px;top:1720px"><div class="service-icon"><div class="fill" role="img" aria-label="Team management icon"></div></div><div class="service-body"><h3>Service Name</h3><p>Sed ut perspiciatis undeise natus error sittsantium</p></div></div>
<div class="abs service" style="left:172px;top:1850px"><div class="service-icon"><div class="fill" role="img" aria-label="Business operations icon"></div></div><div class="service-body"><h3>Service Name</h3><p>Sed ut perspiciatis undeite natus error sittsantium</p></div></div>
<div class="abs service" style="left:477px;top:1850px"><div class="service-icon"><div class="fill" role="img" aria-label="Strategy chart icon"></div></div><div class="service-body"><h3>Service Name</h3><p>Sed ut perspiciatis undeise natus error sittsantium</p></div></div>
<div class="abs service" style="left:781px;top:1850px"><div class="service-icon"><div class="fill" role="img" aria-label="Target goal icon"></div></div><div class="service-body"><h3>Service Name</h3><p>Sed ut perspiciatis undeise natus error sittsantium</p></div></div>

<h2 class="abs section-title" style="left:0;width:1200px;text-align:center;top:2072px">Latest News</h2>

<div class="abs news-photo" style="left:172px;top:2179px;background:linear-gradient(135deg,#dfe3e0,#a9aeb0 60%,#6e6a68)" role="img" aria-label="Colleagues shaking hands in an office"></div>
<h3 class="abs news-title" style="left:393px;top:2186px">Finibus Bonorum et Malorum</h3>
<p class="abs news-text" style="left:393px;top:2241px">Sed ut perspiciatis undloree omnis iste natus error sit voluptatem accusaloren tium doloremque laudantium, totloram rem aperiam, eaque ipsa.</p>
<div class="abs news-date" style="left:393px;top:2329px"><svg width="15" height="14" viewBox="0 0 15 14" fill="none" stroke="#8a8a8a"><rect x=".5" y="2" width="14" height="11.5"/><path d="M.5 5h14M4 0v3M11 0v3"/></svg>JAN 24 2020</div>

<div class="abs news-photo" style="left:614px;top:2179px;background:linear-gradient(135deg,#5a5f68,#2f3440 55%,#a9a49c)" role="img" aria-label="Business people reviewing documents at a meeting table"></div>
<h3 class="abs news-title" style="left:836px;top:2186px">Finibus Bonorum et Malorum</h3>
<p class="abs news-text" style="left:836px;top:2241px">Sed ut perspiciatis undloree omnis iste natus error sit voluptatem accusaloren tium doloremque laudantium, totloram rem aperiam, eaque ipsa.</p>
<div class="abs news-date" style="left:836px;top:2329px"><svg width="15" height="14" viewBox="0 0 15 14" fill="none" stroke="#8a8a8a"><rect x=".5" y="2" width="14" height="11.5"/><path d="M.5 5h14M4 0v3M11 0v3"/></svg>JAN 24 2020</div>

<footer class="abs site-footer"></footer>
<div class="abs social"><span aria-label="Social profile link"></span><span aria-label="Social profile link"></span><span aria-label="Social profile link"></span></div>
<nav class="abs footer-nav"><span>Home</span><span>About Us</span><span>Services</span><span>Industries</span><span>Our Success, Contact.</span></nav>
<p class="abs copyright">Copyright © 2020 Marwick Partners. All Rights Reserved. Sitemap</p>

</body>
</html>
```